Settlewell202.com flyer for window coverings

two sided 8 1/2 x 11 flyer featuring window coverings to send people to our website to shop for window coverings. Can use stock photos of blinds and shutters (wood toned blinds, white shutters, grey roller shades, white faux wood blinds). We don't sell draperies or drapery rods. We do sell other product like lighting and cabinet organization but we would like this flyer to focus on window coverings. We want to be a resource for new home buyers that need items to finish making their new house their home.

Target Market(s)

New home buyers

Industry/Entity Type

Real Estate

Font styles to use
Sans Serif

Requirements
Must have
• photos of window blinds and shades--photos have been added 3/31
• logo of settlewell202.com
• "Settlewell202.com - #1 - Cover your windows for: Privacy, Security, Energy Efficiency. We have all the styles to meet your needs and installation available!"
Should not have
• Pictures of towel bars

```html
<!DOCTYPE html>
<html lang="en">
<head>
<meta charset="utf-8">
<title>Settlewell202.com – Window Coverings</title>
<link href="https://fonts.googleapis.com/css2?family=Source+Sans+3:wght@400;600;700&display=swap" rel="stylesheet">
<style>
  :root {
    --brand-red: #d0202a;
    --ring-grey: #c9c9c9;
    --text-dark: #1c1c1c;
    --white: #ffffff;
    --highlight: #ffe81a;
    --bg-light: #f4f4f4;
    --bg-mid: #dcdcdc;
  }
  html, body {
    margin: 0;
    padding: 0;
    overflow: hidden;
  }
  body {
    width: 927px;
    height: 1200px;
    font-family: "Source Sans 3", sans-serif;
  }
  .flyer {
    position: relative;
    width: 927px;
    height: 1200px;
    overflow: hidden;
    background: var(--white);
  }
  .backdrop {
    position: absolute;
    inset: 0;
    background:
      repeating-linear-gradient(180deg, rgba(255,255,255,0) 0 28px, rgba(200,200,200,0.18) 28px 34px),
      linear-gradient(120deg, var(--bg-light) 0%, var(--white) 35%, var(--bg-mid) 60%, var(--white) 80%, var(--bg-light) 100%);
  }
  .site-url {
    position: absolute;
    top: 16px;
    right: 18px;
    margin: 0;
    font-size: 19px;
    font-weight: 600;
    color: var(--brand-red);
  }
  .brand {
    position: absolute;
    top: 92px;
    left: 68px;
    display: flex;
    align-items: center;
    gap: 14px;
  }
  .brand-dot {
    width: 46px;
    height: 46px;
    border-radius: 50%;
    background: var(--brand-red);
  }
  .brand-name {
    font-size: 40px;
    font-weight: 700;
    color: var(--text-dark);
    letter-spacing: 0.5px;
  }
  .circles {
    position: absolute;
    left: 0;
    top: 0;
  }
  .offer {
    position: absolute;
    left: 61px;
    top: 492px;
    width: 410px;
    color: var(--white);
    font-size: 23px;
    line-height: 31px;
    font-weight: 600;
  }
  .offer p {
    margin: 0 0 31px;
  }
  .offer .discount {
    color: var(--highlight);
    font-weight: 700;
  }
  .gallery {
    position: absolute;
    left: 665px;
    top: 253px;
    width: 262px;
    height: 800px;
    box-sizing: border-box;
    border: 3px solid var(--brand-red);
    display: flex;
    flex-direction: column;
    gap: 3px;
    background: var(--brand-red);
  }
  .gallery-tile {
    flex: 1;
  }
  .tile-wood {
    background: linear-gradient(180deg, #c8651e 0%, #e07a2a 50%, #b3561a 100%);
  }
  .tile-white {
    background: linear-gradient(180deg, #f6f6f6 0%, #e6e6e6 70%, #d9d9d9 100%);
  }
  .tile-dark {
    background: linear-gradient(180deg, #5a2422 0%, #7a3431 45%, #d8d8d8 80%, #c4c4c4 100%);
  }
  .footer-line {
    position: absolute;
    left: 40px;
    bottom: 22px;
    margin: 0;
    font-size: 17.5px;
    font-weight: 600;
    color: var(--text-dark);
  }
  .footer-line .footer-url {
    color: var(--brand-red);
    font-weight: 700;
  }
</style>
</head>
<body>
<main class="flyer">
  <div class="backdrop" role="img" aria-label="Soft light background of white window blinds in daylight"></div>

  <p class="site-url">www.settlewell202.com</p>

  <div class="brand">
    <span class="brand-dot"></span>
    <span class="brand-name">Settlewell 202</span>
  </div>

  <svg class="circles" width="927" height="1200" viewBox="0 0 927 1200" aria-hidden="true">
    <circle cx="224" cy="678" r="392" fill="var(--ring-grey)" opacity="0.75"/>
    <circle cx="170" cy="678" r="342" fill="var(--brand-red)"/>
  </svg>

  <section class="offer">
    <p>Your builder and their supplier have partner together to offer you this special <span class="discount">10% discount</span> on a wide variety of window blinds and shades along with other products to finish making your house your home.</p>
    <p>We offer faux wood blinds, roller shades, verticals, faux wood shutters, sliding panels and honey comb shades in a variety of colors and finishes.</p>
  </section>

  <div class="gallery">
    <div class="gallery-tile tile-wood" role="img" aria-label="Wood toned horizontal blinds"></div>
    <div class="gallery-tile tile-white" role="img" aria-label="White faux wood blinds above a windowsill with vases"></div>
    <div class="gallery-tile tile-dark" role="img" aria-label="Dark wood blinds behind a sofa with cushions"></div>
  </div>

  <p class="footer-line">Visit us at: <span class="footer-url">www.settlewell202.com.</span>&nbsp; Live chat available to answer any questions you might have.</p>
</main>
</body>
</html>
```